A clean crisp business card for a Landscape Construction company. Designed to be easy to read contact/ info and also be appealing/interesting, unlike a traditional business card.

Industry/Entity Type

Landscape Construction

Contact Information for Business Card

Company name : Brambleford Landscape Construction, phone number: (877) 62Vista, website:Bramblefordyards.example, Email, sales@bramblefordyards.example

Requirements
Nice to have
• Luxurious finishes/ details…. Icons or emblems next to contact info
Should not have
• Clipart or general pictures

```html
<!DOCTYPE html>
<html lang="en">
<head>
<meta charset="utf-8">
<title>Brambleford Landscape Construction – Business Card</title>
<link href="https://fonts.googleapis.com/css2?family=Arimo:wght@400&family=Libre+Baskerville:wght@700&display=swap" rel="stylesheet">
<style>
  :root {
    --page-bg: #141414;
    --card-bg: #232323;
    --brand-blue: #1f6cc4;
    --brand-green: #8cc63f;
    --text-light: #f2f2f2;
    --text-muted: #d6d6d6;
  }
  * { margin: 0; padding: 0; box-sizing: border-box; }
  html, body {
    width: 1200px; height: 900px; overflow: hidden;
    background: var(--page-bg);
  }
  .stage {
    width: 1200px; height: 900px;
    display: flex; align-items: center; justify-content: center;
  }
  .business-card {
    position: relative;
    width: 1000px; height: 572px;
    background: var(--card-bg);
    border-radius: 34px;
    overflow: hidden;
    font-family: "Arimo", Arial, sans-serif;
    color: var(--text-light);
  }
  .person {
    position: absolute; left: 70px; top: 120px;
  }
  .person-name {
    font-family: "Libre Baskerville", Georgia, serif;
    font-weight: 700; font-size: 40px; letter-spacing: 1px;
    text-transform: uppercase; line-height: 1;
  }
  .person-name .first { color: var(--brand-blue); }
  .person-name .last { color: var(--brand-green); }
  .person-role {
    margin-top: 10px; font-size: 25px; color: var(--text-light);
  }
  .divider {
    position: absolute; left: 70px; top: 222px;
    width: 860px; height: 2px;
    background: linear-gradient(90deg, var(--brand-blue), var(--brand-green));
  }
  .contact-list {
    position: absolute; left: 70px; top: 258px;
    list-style: none;
  }
  .contact-item {
    display: flex; align-items: center; gap: 12px;
    font-size: 25px; line-height: 1; margin-bottom: 14px;
  }
  .contact-icon { width: 22px; height: 22px; flex: none; }
  .brand-name {
    position: absolute; right: 80px; top: 110px;
    text-align: right; color: var(--brand-blue);
    font-size: 34px; line-height: 1.25;
  }
  .address {
    position: absolute; right: 80px; top: 292px;
    text-align: right; font-size: 26px; line-height: 1.45;
    color: var(--text-light);
  }
  .edge-band {
    position: absolute; left: 0; bottom: 0;
    width: 100%; height: 16px;
  }
</style>
</head>
<body>
<main class="stage">
  <article class="business-card">
    <header class="person">
      <h1 class="person-name"><span class="first">Owen</span> <span class="last">Hartley</span></h1>
      <p class="person-role">Founder</p>
    </header>

    <div class="divider"></div>

    <ul class="contact-list">
      <li class="contact-item">
        <svg class="contact-icon" viewBox="0 0 24 24"><path fill="#f2f2f2" d="M3 8c0-2 2-3 9-3s9 1 9 3v2h-5V8H8v2H3z M6 11h12l2 8H4z"/><circle cx="12" cy="15" r="2.2" fill="#232323"/></svg>
        <span>(877) 62Vista</span>
      </li>
      <li class="contact-item">
        <svg class="contact-icon" viewBox="0 0 24 24"><rect x="2" y="5" width="20" height="14" rx="1.5" fill="#f2f2f2"/><path d="M2.5 6l9.5 7 9.5-7" fill="none" stroke="#232323" stroke-width="1.6"/></svg>
        <span>sales@bramblefordyards.example</span>
      </li>
      <li class="contact-item">
        <svg class="contact-icon" viewBox="0 0 24 24"><circle cx="12" cy="12" r="10" fill="#f2f2f2"/><path d="M7 7c2 1 3 3 2 5s1 3 2 5M15 5c-1 2 1 3 3 3M14 13c2 0 3 2 2 4" fill="none" stroke="#232323" stroke-width="1.6"/></svg>
        <span>bramblefordyards.example</span>
      </li>
    </ul>

    <div class="brand-name">Brambleford<br>Landscape Construction</div>

    <address class="address" style="font-style:normal">
      4120 S. Marlow Avenue<br>
      Country Name, AB 40612
    </address>

    <svg class="edge-band" viewBox="0 0 1000 16" preserveAspectRatio="none">
      <polygon points="0,0 470,0 486,16 0,16" fill="var(--brand-green)"/>
      <polygon points="470,0 1000,0 1000,16 486,16" fill="var(--brand-blue)"/>
    </svg>
  </article>
</main>
</body>
</html>
```